Business card for my new company (Accounting firm)

I need a business card for my new business Brightwell Advisory and Ledger SA. Our services are accounting, tax, audit and financial management. Our customers are small companies, start-ups and new companies. The final design has to show financial security, trust and growth. Please find our logo attached to the business card. Text for the business card: Brightwell Advisory and Ledger SA Tomas Varenholt Director and Founder Certified Accountant Tel. 022 418 57 34 tv@clairevalconseil.ch www.clairevalconseil.ch Rue des Vergières 27 1201 Geneva
Target Market(s)
Our customers are small companies, start-ups and new companies.
Industry/Entity Type
Finance And Accounting
Contact Information for Business Card
Claireval Conseil et Comptes SA
Tomas Varenholt
Directeur et Fondateur
Expert-comptable diplômé
Tél. 022 418 57 34
tv@clairevalconseil.ch
www.clairevalconseil.ch
Rue des Vergières 27
1201 Genève

```html
<!DOCTYPE html>
<html lang="fr">
<head>
<meta charset="utf-8">
<title>Claireval Conseil et Comptes SA – Carte de visite</title>
<link rel="stylesheet" href="https://fonts.googleapis.com/css2?family=Roboto:wght@400;500;700&display=swap">
<style>
  :root {
    --backdrop: #232222;
    --paper: #ffffff;
    --brand-blue: #1a6490;
    --sky-blue: #35b0e2;
    --ink: #3d3d3d;
    --ink-soft: #4a4a4a;
    --white: #ffffff;
  }
  * { margin: 0; padding: 0; box-sizing: border-box; }
  html, body {
    width: 1125px; height: 1200px; overflow: hidden;
    background: var(--backdrop);
    font-family: "Roboto", Arial, sans-serif;
  }
  .canvas { position: relative; width: 1125px; height: 1200px; }
  .card {
    position: absolute; left: 171px; width: 826px; height: 472px;
    overflow: hidden;
  }
  .card--front { top: 106px; background: var(--paper); }
  .card--back { top: 639px; background: var(--brand-blue); }

  .wordmark { position: absolute; text-align: right; font-weight: 500; }
  .card--front .wordmark { right: 50px; top: 108px; color: var(--ink); }
  .wordmark__name { display: block; font-size: 58px; letter-spacing: 4px; line-height: 1; }
  .wordmark__tagline { display: block; font-size: 21px; letter-spacing: 3px; margin-top: 12px; }

  .accent-top {
    position: absolute; left: 0; top: 262px; width: 350px; height: 14px;
    background: var(--sky-blue); border-radius: 0 14px 0 0;
  }
  .accent-bottom {
    position: absolute; right: 0; top: 376px; width: 313px; height: 14px;
    background: var(--sky-blue); border-radius: 0 0 0 14px;
  }
  .band {
    position: absolute; left: 0; top: 268px; width: 826px; height: 124px;
    background: var(--brand-blue); color: var(--white);
  }
  .person { position: absolute; left: 45px; top: 14px; }
  .person__name { font-size: 30px; font-weight: 700; line-height: 36px; }
  .person__role { font-size: 20.5px; line-height: 27px; }

  .contacts { position: absolute; right: 46px; top: 21px; list-style: none; text-align: right; }
  .contacts li {
    display: flex; justify-content: flex-end; align-items: center;
    font-size: 20px; line-height: 27px;
  }
  .contacts svg { width: 18px; height: 18px; margin-left: 9px; fill: var(--white); }

  .address {
    position: absolute; left: 42px; top: 406px; display: flex; align-items: center;
    font-size: 20px; color: var(--ink-soft);
  }
  .address svg { width: 18px; height: 24px; margin-right: 8px; fill: var(--brand-blue); }

  .card--back .wordmark {
    left: 0; right: 0; top: 282px; text-align: center; color: var(--white);
  }
  .card--back .wordmark__name { font-size: 52px; }
  .card--back .wordmark__tagline { font-size: 17px; margin-top: 10px; }
</style>
</head>
<body>
<main class="canvas">
  <section class="card card--front" aria-label="Recto de la carte">
    <div class="wordmark">
      <span class="wordmark__name">CLAIREVAL</span>
      <span class="wordmark__tagline">CONSEIL ET COMPTES</span>
    </div>

    <div class="accent-top"></div>
    <div class="accent-bottom"></div>
    <div class="band">
      <div class="person">
        <p class="person__name">Tomas Varenholt</p>
        <p class="person__role">Directeur et Fondateur</p>
        <p class="person__role">Expert-comptable diplômé</p>
      </div>
      <ul class="contacts">
        <li>022 418 57 34
          <svg viewBox="0 0 24 24" aria-hidden="true"><path d="M6.6 10.8a15.1 15.1 0 0 0 6.6 6.6l2.2-2.2c.3-.3.7-.4 1-.2 1.1.4 2.3.6 3.6.6.6 0 1 .4 1 1V20c0 .6-.4 1-1 1A17 17 0 0 1 3 4c0-.6.4-1 1-1h3.5c.6 0 1 .4 1 1 0 1.3.2 2.5.6 3.6.1.3 0 .7-.2 1z"/></svg>
        </li>
        <li>tv@clairevalconseil.ch
          <svg viewBox="0 0 24 24" aria-hidden="true"><path d="M2 5h20v14H2z" opacity="0"/><path d="M2 5h20v2l-10 6L2 7zM2 9l10 6 10-6v10H2z"/></svg>
        </li>
        <li>www.clairevalconseil.ch
          <svg viewBox="0 0 24 24" aria-hidden="true"><path d="M12 2a10 10 0 1 0 0 20 10 10 0 0 0 0-20zm-1 17.9A8 8 0 0 1 4.2 10L9 14.8v1a2 2 0 0 0 2 2zm6.9-2.5A2 2 0 0 0 16 16h-1v-3a1 1 0 0 0-1-1H8v-2h2a1 1 0 0 0 1-1V7h2a2 2 0 0 0 2-2v-.4a8 8 0 0 1 2.9 12.8z"/></svg>
        </li>
      </ul>
    </div>

    <p class="address">
      <svg viewBox="0 0 18 24" aria-hidden="true"><path d="M9 0a9 9 0 0 0-9 9c0 6.8 9 15 9 15s9-8.2 9-15a9 9 0 0 0-9-9zm0 12.5A3.5 3.5 0 1 1 9 5.5a3.5 3.5 0 0 1 0 7z"/></svg>
      Rue des Vergières 27, 1201 Genève
    </p>
  </section>

  <section class="card card--back" aria-label="Verso de la carte">
    <div class="wordmark">
      <span class="wordmark__name">CLAIREVAL</span>
      <span class="wordmark__tagline">CONSEIL ET COMPTES</span>
    </div>
  </section>
</main>
</body>
</html>
```